Stonebrace Business Card Design

The Stonebrace Co is an aggregate (crushing) equipment dealer serving Western Canadian provinces. Stonebrace is a distributor of aggregate equipment for different manufacturers.

We are looking to change and update the existing business card which has been used since the existence of the company. A copy of existing card has been attached for reference. The Stonebrace Co logo we want to remain the same and we want the green color to remain the same.

We are wanting something new with a different look. A refreshing card to show a new modern and updated look. No longer wanting to have the manufacturers on the back of the card but something more like our logo on the back of the card with a statement like "Quarry Equipment"

ideas could be:
- card can be different colors on front and back
- front or reverse of the card could possibly be the green color with the logo in black

Target Market(s)

Owners of Aggregate/Crushing companies

Contact Information for Business Card

see above

Requirements
Must have
• - logo to remain same along with same font within logo
• - green color to remain same
Nice to have
• as noted above under project description
Should not have

```html
<!DOCTYPE html>
<html lang="en">
<head>
<meta charset="utf-8">
<title>Stonebrace Business Card</title>
<link rel="stylesheet" href="https://fonts.googleapis.com/css2?family=Roboto:wght@400;500;700&display=swap">
<style>
  :root {
    --brand-green: #868a0b;
    --ink-dark: #252324;
    --card-white: #f3f3f3;
    --text-light: #ffffff;
    --backdrop: #e4e1dc;
  }
  * { margin: 0; padding: 0; box-sizing: border-box; }
  html, body { width: 1200px; height: 960px; overflow: hidden; }
  body {
    background: var(--backdrop);
    font-family: "Roboto", Arial, sans-serif;
    position: relative;
  }
  .card {
    position: absolute;
    left: 320px;
    width: 600px;
    height: 345px;
    border-radius: 20px;
    overflow: hidden;
  }
  .card-front {
    top: 100px;
    background: var(--brand-green);
  }
  .front-brand {
    position: absolute;
    left: 0; right: 0; top: 150px;
    display: flex;
    align-items: center;
    justify-content: center;
    gap: 18px;
  }
  .brand-dot {
    width: 44px; height: 44px;
    border-radius: 50%;
    background: var(--ink-dark);
  }
  .front-brand .brand-name {
    font-weight: 700;
    font-size: 22px;
    color: var(--ink-dark);
    letter-spacing: 0.2px;
  }
  .tagline {
    position: absolute;
    left: 0; right: 0; top: 299px;
    text-align: center;
    font-weight: 700;
    font-size: 14.5px;
    color: var(--ink-dark);
  }
  .card-back {
    top: 493px;
    height: 343px;
    background: var(--card-white);
  }
  .back-shape { position: absolute; inset: 0; }
  .back-brand .brand-dot {
    position: absolute;
    left: 117px; top: 40px;
    width: 64px; height: 64px;
    background: var(--brand-green);
  }
  .back-brand .brand-name {
    position: absolute;
    left: 35px; top: 143px;
    font-weight: 700;
    font-size: 20px;
    color: var(--ink-dark);
  }
  .contact {
    position: absolute;
    right: 25px; top: 128px;
    text-align: right;
    color: var(--text-light);
  }
  .person-name {
    font-weight: 500;
    font-size: 20px;
    color: var(--brand-green);
    line-height: 24px;
  }
  .person-title {
    font-weight: 500;
    font-size: 14px;
    line-height: 20px;
    margin-bottom: 8px;
  }
  .address { font-size: 13.5px; line-height: 19px; margin-bottom: 8px; }
  .contact-line {
    display: flex;
    justify-content: flex-end;
    align-items: center;
    gap: 8px;
    font-size: 13.5px;
    line-height: 19.3px;
  }
  .contact-icon { width: 13px; height: 13px; fill: var(--brand-green); }
</style>
</head>
<body>

<section class="card card-front">
  <div class="front-brand">
    <span class="brand-dot"></span>
    <span class="brand-name">THE STONEBRACE CO.</span>
  </div>
  <p class="tagline">Quarry Equipment</p>
</section>

<section class="card card-back">
  <svg class="back-shape" width="600" height="343" viewBox="0 0 600 343">
    <path d="M380,0 C372,140 285,290 150,343 L600,343 L600,0 Z" fill="var(--ink-dark)"/>
    <path d="M410,15 C404,160 330,285 160,343 C342,286 416,165 410,15 Z" fill="var(--card-white)"/>
  </svg>

  <div class="back-brand">
    <span class="brand-dot"></span>
    <span class="brand-name">THE STONEBRACE CO.</span>
  </div>

  <div class="contact">
    <p class="person-name">DALE MORVEN</p>
    <p class="person-title">CEO/FOUNDER</p>
    <p class="address">2210- 48B Avenue<br>Nisku, Alberta T9E 3K1</p>
    <p class="contact-line">780.555.0142
      <svg class="contact-icon" viewBox="0 0 16 16"><path d="M3 1l3 3-1.5 2a9 9 0 0 0 5.5 5.5L12 10l3 3-2 2C7 15 1 9 1 3z"/></svg></p>
    <p class="contact-line">780.555.0178
      <svg class="contact-icon" viewBox="0 0 16 16"><path d="M4 0h8v16H4zM5.5 2v10h5V2zM7 13h2v1.5H7z" fill-rule="evenodd"/></svg></p>
    <p class="contact-line">780.555.0193
      <svg class="contact-icon" viewBox="0 0 16 16"><path d="M4 1h8v4H4zM1 6h14v7h-3v2H4v-2H1zM5 10v4h6v-4z" fill-rule="evenodd"/></svg></p>
    <p class="contact-line">dale@stonebr.com
      <svg class="contact-icon" viewBox="0 0 16 16"><path d="M1 3h14v10H1zM2.5 4.5L8 9l5.5-4.5z" fill-rule="evenodd"/></svg></p>
    <p class="contact-line">www.stonebrace.ca
      <svg class="contact-icon" viewBox="0 0 16 16"><circle cx="8" cy="8" r="7"/><path d="M1 8h14M8 1c-3 3-3 11 0 14M8 1c3 3 3 11 0 14" stroke="var(--ink-dark)" stroke-width="1.2" fill="none"/></svg></p>
  </div>
</section>

</body>
</html>
```